Meadowlark Property Review is a leading provider of residential appraisal and home inspection products in S

I need a business card/logo designed that obviously describes my business. We are a residential appraisal and home inspection company in Springfield, MO. We offer residential appraisals, home inspection, pest inspection and radon gas measurement. We have been in business for 18 years and hold state certified residential appraisal licenses and OBREX certified home inspection licenses. I have a logo that I really like and will attach, but would be open to new suggestions. I like more modern designs than traditional and would like a two sided card with our services, licenses and qualifications on the back.

```html
<!DOCTYPE html>
<html lang="en">
<head>
<meta charset="utf-8">
<title>Meadowlark Property Review – Business Card</title>
<link href="https://fonts.googleapis.com/css2?family=Open+Sans:wght@400;600;700;800&display=swap" rel="stylesheet">
<style>
  :root{
    --stage:#ecebe8;
    --white:#ffffff;
    --orange-light:#f9ad45;
    --orange:#f28a22;
    --orange-deep:#ec7318;
    --brown:#6e5235;
    --brown-light:#a08465;
    --brown-dark:#4f3a25;
    --ink:#2a2016;
    --text-on-dark:#fbf6ef;
    --badge:#c9a43a;
  }
  *{margin:0;padding:0;box-sizing:border-box}
  html,body{width:1200px;height:913px;overflow:hidden}
  body{
    background:var(--stage);
    font-family:"Open Sans",Arial,sans-serif;
    position:relative;
  }
  .card{
    position:absolute;left:250px;width:700px;height:400px;
    border-radius:26px;overflow:hidden;
    box-shadow:0 10px 30px rgba(0,0,0,.18);
  }
  .card--front{top:40px;background:var(--white)}
  .card--back{top:473px;background:linear-gradient(135deg,var(--brown-light) 0%,var(--brown) 55%,var(--brown-dark) 100%)}
  .card__art{position:absolute;inset:0}

  /* front */
  .front__address{
    position:absolute;left:40px;top:42px;width:300px;
    font-weight:700;font-size:17px;line-height:1.35;color:var(--ink);
  }
  .badge{
    position:absolute;left:44px;top:196px;width:40px;height:40px;border-radius:50%;
    background:var(--badge);
  }
  .brand{
    position:absolute;display:flex;align-items:center;gap:10px;
    font-weight:800;letter-spacing:.01em;line-height:1.05;
  }
  .brand__mark{width:16px;height:16px;flex:none}
  .brand--front{left:110px;top:186px;color:var(--brown);font-size:25px;width:250px}
  .brand--front .brand__mark{background:var(--orange)}

  .contact{
    position:absolute;right:38px;top:78px;text-align:right;color:var(--ink);
  }
  .contact__name{font-weight:800;font-size:24px;letter-spacing:.02em}
  .contact__role{font-weight:600;font-size:13px;color:var(--white);letter-spacing:.08em;margin:2px 0 16px}
  .contact__list{list-style:none}
  .contact__item{
    display:flex;justify-content:flex-end;align-items:center;gap:8px;
    font-weight:600;font-size:16px;line-height:1.55;
  }
  .contact__icon{width:16px;height:16px;flex:none}

  /* back */
  .back__intro{
    position:absolute;left:46px;top:36px;width:520px;
    font-size:11.5px;font-weight:600;line-height:1.45;color:var(--text-on-dark);
  }
  .brand--back{left:60px;top:170px;color:var(--text-on-dark);font-size:30px;width:300px}
  .brand--back .brand__mark{background:var(--orange-light);width:20px;height:20px}
  .services{
    position:absolute;right:36px;top:118px;list-style:none;text-align:right;
  }
  .services__item{
    display:flex;justify-content:flex-end;align-items:center;gap:12px;
    font-size:18px;font-weight:600;letter-spacing:.03em;line-height:1.4;color:var(--text-on-dark);
  }
  .services__item::after{
    content:"";width:10px;height:10px;border-radius:50%;background:var(--orange-light);flex:none;
  }
</style>
</head>
<body>

<section class="card card--front" aria-label="Business card front">
  <svg class="card__art" viewBox="0 0 700 400" preserveAspectRatio="none" aria-hidden="true">
    <defs>
      <linearGradient id="frontOrange" x1="0" y1="0" x2="1" y2="1">
        <stop offset="0" stop-color="#f9b04a"/>
        <stop offset="1" stop-color="#ec7318"/>
      </linearGradient>
    </defs>
    <path d="M548 0 C470 150 330 320 150 400 L700 400 L700 0 Z" fill="#6e5235"/>
    <path d="M566 0 C490 160 360 330 190 400 L700 400 L700 0 Z" fill="url(#frontOrange)"/>
  </svg>

  <p class="front__address">Meadowlark Property Review 4410 E Sunshine Street Suite C Springfield, MO 65809</p>
  <span class="badge" role="img" aria-label="OBREX certification badge"></span>
  <div class="brand brand--front"><span class="brand__mark"></span>Meadowlark Property Review</div>

  <div class="contact">
    <h1 class="contact__name">DANA WHITFIELD</h1>
    <p class="contact__role">OWNER</p>
    <ul class="contact__list">
      <li class="contact__item">417-555-0142
        <svg class="contact__icon" viewBox="0 0 16 16"><path d="M4 1.5l2.5 3-1.5 1.7a8 8 0 004.8 4.8l1.7-1.5 3 2.5-1.8 2.3C7.5 14 2 8.5 1.7 3.3z" fill="#2a2016"/></svg></li>
      <li class="contact__item">417-555-0178
        <svg class="contact__icon" viewBox="0 0 16 16"><path d="M4 1.5l2.5 3-1.5 1.7a8 8 0 004.8 4.8l1.7-1.5 3 2.5-1.8 2.3C7.5 14 2 8.5 1.7 3.3z" fill="#2a2016"/></svg></li>
      <li class="contact__item">info@meadowlarkreview.com
        <svg class="contact__icon" viewBox="0 0 16 16"><rect x="1.5" y="3.5" width="13" height="9" rx="1" fill="none" stroke="#2a2016" stroke-width="1.5"/><path d="M1.5 4l6.5 5 6.5-5" fill="none" stroke="#2a2016" stroke-width="1.5"/></svg></li>
      <li class="contact__item">www.meadowlarkreview.com
        <svg class="contact__icon" viewBox="0 0 16 16"><circle cx="8" cy="8" r="6.5" fill="none" stroke="#2a2016" stroke-width="1.4"/><ellipse cx="8" cy="8" rx="2.8" ry="6.5" fill="none" stroke="#2a2016" stroke-width="1.2"/><path d="M1.5 8h13" stroke="#2a2016" stroke-width="1.2"/></svg></li>
    </ul>
  </div>
</section>

<section class="card card--back" aria-label="Business card back">
  <p class="back__intro">With years of experience behind us, we're prepared to tackle anything from a first time buyer's starter home or a seasoned buyer purchasing a luxurious dream home</p>
  <div class="brand brand--back"><span class="brand__mark"></span>Meadowlark Property Review</div>
  <ul class="services">
    <li class="services__item">APPRAISAL</li>
    <li class="services__item">HOME INSPECTION</li>
    <li class="services__item">TERMITE</li>
    <li class="services__item">RADON</li>
    <li class="services__item">WELL &amp; SEPTIC INSPECTION</li>
    <li class="services__item">ENERGY AUDITS</li>
  </ul>
</section>

</body>
</html>
```